Veltrane Group Business Card Design

The CEO is looking for a new trendy look for his business card.
You can stay with current branding or come up with something new/creative. It can be 3D, including Medical Office buildings. You can use our logo in a variety of colors. Please include name, title, company name, company website, email address, cell number

Target Market(s)

Real Estate Development and Construction

Industry/Entity Type

Health care real estate

Contact Information for Business Card

Rohesh Kamdar, CEO M-604.781.2249 E-roheshkamdar@veltrane.com Address:4180 Lindqvist Ave, Tampa, FL 33482 www.veltrane.com

Font styles to use
Other font styles liked:
• Be creative

Requirements
Must have
• Creative, trendy look
Nice to have
• Please go to our website to get a feel- www. veltrane.com
Should not have
• small fonts

```html
<!DOCTYPE html>
<html lang="en">
<head>
<meta charset="utf-8">
<title>Veltrane Group Business Card</title>
<link href="https://fonts.googleapis.com/css2?family=Arimo:wght@400;700&display=swap" rel="stylesheet">
<style>
  :root {
    --backdrop: #ebebea;
    --paper: #f6f6f5;
    --ink-red: #b01c26;
    --ink-grey: #4a4a4a;
    --rule-grey: #8c8c8c;
    --card-dark: #2e2e2f;
    --card-darker: #222223;
  }
  * { margin: 0; padding: 0; box-sizing: border-box; }
  html, body {
    width: 1200px; height: 801px; overflow: hidden;
    background: var(--backdrop);
    font-family: "Arimo", Arial, sans-serif;
  }
  .canvas {
    position: relative; width: 1200px; height: 801px;
    display: flex; align-items: center; justify-content: center; gap: 40px;
  }
  .card {
    position: relative; width: 540px; height: 309px; overflow: hidden;
    border-bottom: 4px solid var(--ink-red);
    box-shadow: 0 10px 24px rgba(0,0,0,0.18);
  }
  /* Company name placeholder */
  .company-name {
    display: flex; align-items: center; gap: 10px;
    color: var(--ink-red); font-weight: 700; white-space: nowrap;
  }
  .company-name__square {
    width: 14px; height: 14px; background: var(--ink-red); flex: none;
  }
  /* Front */
  .card--front {
    background: var(--paper);
    display: flex; align-items: center;
    padding: 0 30px 0 34px;
  }
  .card--front .company-name { width: 200px; font-size: 24px; }
  .divider {
    width: 1px; height: 150px; background: var(--rule-grey);
    margin: 0 22px 0 8px; flex: none;
  }
  .contact { color: var(--ink-grey); font-size: 15px; line-height: 1.32; }
  .contact__name {
    color: var(--ink-red); font-weight: 700; font-size: 19px;
    letter-spacing: 0.3px; text-transform: uppercase;
  }
  .contact__title { margin-bottom: 8px; }
  .contact__address { margin-bottom: 8px; }
  .contact__line { display: flex; align-items: center; gap: 7px; white-space: nowrap; }
  .contact__line svg { width: 12px; height: 12px; flex: none; }
  /* Back */
  .card--back {
    background: linear-gradient(160deg, var(--card-dark), var(--card-darker));
    display: flex; align-items: center; justify-content: center;
  }
  .card--back .company-name { font-size: 44px; gap: 14px; }
  .card--back .company-name__square { width: 22px; height: 22px; }
</style>
</head>
<body>
<main class="canvas">
  <section class="card card--front" aria-label="Business card front">
    <div class="company-name">
      <span class="company-name__square" aria-hidden="true"></span>
      <span>Veltrane Group</span>
    </div>
    <div class="divider"></div>
    <div class="contact">
      <p class="contact__name">Rohesh Kamdar</p>
      <p class="contact__title">CEO</p>
      <p class="contact__address">4180 Lindqvist Ave<br>Tampa, FL 33482</p>
      <p class="contact__line">
        <svg viewBox="0 0 12 12" aria-hidden="true"><path fill="#b01c26" d="M1 4c0-2 2-3 5-3s5 1 5 3l-2 1-1-2H4L3 5 1 4zm2 2h6l1 5H2z"/></svg>
        604.781.2249
      </p>
      <p class="contact__line">
        <svg viewBox="0 0 12 12" aria-hidden="true"><path fill="#b01c26" d="M1 3h10v7H1z"/><path fill="none" stroke="#fff" stroke-width="1" d="M1 3l5 4 5-4"/></svg>
        roheshkamdar@veltrane.com
      </p>
      <p class="contact__line">
        <svg viewBox="0 0 12 12" aria-hidden="true"><circle cx="6" cy="6" r="5" fill="#b01c26"/><path fill="none" stroke="#fff" stroke-width="0.8" d="M1 6h10M6 1c-2 3-2 7 0 10M6 1c2 3 2 7 0 10"/></svg>
        www.veltrane.com
      </p>
    </div>
  </section>

  <section class="card card--back" aria-label="Business card back">
    <div class="company-name">
      <span class="company-name__square" aria-hidden="true"></span>
      <span>Veltrane Group</span>
    </div>
  </section>
</main>
</body>
</html>
```